High-end construction company needs a business card design

We need a modern looking business card that draws people in, is memorable and looks so good people will want to sick it on their fridges.
On the first side what is needed are:
Logo
My name - Tomasz Brelwik
Title - Managing Director
Website - www.varkelt.co.uk
Email - tomasz@varkelt.co.uk
Telephone - 020 5194 6281
Mobile - 07845139072
On the back side was is needed is a list of all the services we provide:
-Kitchen Renovations
-Bathroom Renovations
-House Renovations
-Garage Conversions
-Extensions
-Loft Conversions
-Conservatories
-Carpentry
-Tiling
-Electrical
-Plumbing & Heating
-Bricklaying
-Landscaping
-Decorating
-Plastering
We would like the colours to be the same shades as on the logo with grey or black for the words.
Target Market(s)
Anyone who needs building work done
Contact Information for Business Card
This business card is for a construction company which strives to deliver excellent service and quality.
The look and feel of the card should represent this.
Requirements
Must have
- On the first side what is needed are:
Logo
My name - Tomasz Brelwik
Title - Managing Director
Website - www.varkelt.co.uk
Email - tomasz@varkelt.co.uk
Telephone - 020 5194 6281
Mobile - 07845139072
Nice to have
- Cool looking features

```html
<!DOCTYPE html>
<html lang="en">
<head>
<meta charset="utf-8">
<title>Varkelt Construction Ltd – Business Card</title>
<link rel="stylesheet" href="https://fonts.googleapis.com/css2?family=Montserrat:wght@400;500;700&display=swap">
<style>
  :root {
    --backdrop: #3b322e;
    --card: #1b1b1b;
    --green: #5fd13a;
    --green-deep: #3f9f2a;
    --ink: #f2f2f2;
    --muted: #cfcfcf;
  }
  * { box-sizing: border-box; margin: 0; padding: 0; }
  html, body {
    width: 1200px; height: 716px; overflow: hidden;
    background: var(--backdrop);
    font-family: "Montserrat", sans-serif;
  }
  .canvas { position: relative; width: 1200px; height: 716px; }

  .card {
    position: absolute;
    width: 540px; height: 309px;
    background: var(--card);
    border-right: 4px solid var(--green);
    border-bottom: 4px solid var(--green);
    box-shadow: 0 14px 30px rgba(0,0,0,.45);
  }
  .card--back { left: 40px; top: 70px; }
  .card--front { left: 620px; top: 330px; }

  /* Brand lockup */
  .brand { position: absolute; display: flex; align-items: center; gap: 12px; color: var(--green); }
  .brand__mark { width: 22px; height: 22px; background: var(--green); flex: none; }
  .brand__name { font-weight: 700; font-size: 34px; line-height: 1; letter-spacing: 1px; text-transform: uppercase; }
  .brand__sub { font-weight: 700; font-size: 13px; letter-spacing: 4px; text-transform: uppercase; margin-top: 6px; }
  .card--back .brand { right: 40px; bottom: 46px; }
  .card--front .brand { left: 34px; top: 128px; }

  /* Services list */
  .services { position: absolute; left: 34px; top: 26px; list-style: none; }
  .services li {
    display: flex; align-items: center; gap: 10px;
    color: var(--ink); font-size: 11.5px; line-height: 16.5px;
  }
  .services li::before {
    content: ""; width: 6px; height: 6px; border-radius: 50%;
    background: var(--green); flex: none;
  }

  /* Front contact block */
  .divider {
    position: absolute; left: 300px; top: 48px;
    width: 2px; height: 214px; background: var(--green-deep);
  }
  .contact { position: absolute; left: 322px; top: 62px; color: var(--ink); }
  .contact__name { color: var(--green); font-weight: 700; font-size: 19px; }
  .contact__title { font-size: 12.5px; margin: 3px 0 14px; color: var(--muted); }
  .contact__address { font-size: 12.5px; line-height: 17px; margin-bottom: 8px; }
  .contact__line { display: flex; align-items: center; gap: 7px; font-size: 12.5px; line-height: 19px; }
  .contact__line svg { width: 10px; height: 10px; flex: none; }
</style>
</head>
<body>
<main class="canvas">

  <section class="card card--back" aria-label="Card back: services">
    <ul class="services">
      <li>Kitchen Renovations</li>
      <li>Bathroom Renovations</li>
      <li>House Renovations</li>
      <li>Garage Conversions</li>
      <li>Extensions</li>
      <li>Loft Conversions</li>
      <li>Conservatories</li>
      <li>Carpentry</li>
      <li>Tiling</li>
      <li>Electrical</li>
      <li>Plumbing &amp; Heating</li>
      <li>Bricklaying</li>
      <li>Landscaping</li>
      <li>Decorating</li>
      <li>Plastering</li>
    </ul>
    <div class="brand">
      <span class="brand__mark"></span>
      <div>
        <div class="brand__name">Varkelt</div>
        <div class="brand__sub">Construction Ltd</div>
      </div>
    </div>
  </section>

  <section class="card card--front" aria-label="Card front: contact">
    <div class="brand">
      <span class="brand__mark"></span>
      <div>
        <div class="brand__name">Varkelt</div>
        <div class="brand__sub">Construction Ltd</div>
      </div>
    </div>
    <div class="divider"></div>
    <div class="contact">
      <div class="contact__name">Tomasz Brelwik</div>
      <div class="contact__title">Managing Director</div>
      <div class="contact__address">14-16 Harlow Street,<br>London, E2 6RT</div>
      <div class="contact__line">
        <svg viewBox="0 0 10 10" aria-hidden="true"><path d="M2 1 L4 1 L4.6 3 L3.4 3.8 Q4.2 5.8 6.2 6.6 L7 5.4 L9 6 L9 8 Q5 9 1.6 5 Q1 3 2 1Z" fill="var(--green)"/></svg>
        020 5194 6281
      </div>
      <div class="contact__line">
        <svg viewBox="0 0 10 10" aria-hidden="true"><rect x="2.5" y="0.8" width="5" height="8.4" rx="1" fill="none" stroke="var(--green)" stroke-width="1.1"/><circle cx="5" cy="7.6" r=".6" fill="var(--green)"/></svg>
        07845139072
      </div>
      <div class="contact__line">
        <svg viewBox="0 0 10 10" aria-hidden="true"><rect x=".8" y="2" width="8.4" height="6" fill="none" stroke="var(--green)" stroke-width="1"/><path d="M.8 2 L5 5.5 L9.2 2" fill="none" stroke="var(--green)" stroke-width="1"/></svg>
        tomasz@varkelt.co.uk
      </div>
      <div class="contact__line">
        <svg viewBox="0 0 10 10" aria-hidden="true"><circle cx="5" cy="5" r="4.2" fill="none" stroke="var(--green)" stroke-width="1"/><ellipse cx="5" cy="5" rx="1.8" ry="4.2" fill="none" stroke="var(--green)" stroke-width=".8"/><path d="M.8 5 H9.2" stroke="var(--green)" stroke-width=".8"/></svg>
        www.varkelt.co.uk
      </div>
    </div>
  </section>

</main>
</body>
</html>
```